Business Card Design Project

I require a business card with the following information on them for various different people;
name
m:
f:
e:
I have a logo already and will attached that. We are in the construction industry. I require something clean and simple but eye catching at the same time. You can use another colour with our logo if you like and you can style the logo as well if you wish. I am open.
Also it needs to be front and back design.
Industry/Entity Type
Construction
Requirements
Must have
- Logo, name, mobile, fax and email address.
Front and back design

```html
<!DOCTYPE html>
<html lang="en">
<head>
<meta charset="utf-8">
<title>Oakridge Developments – Business Card</title>
<link href="https://fonts.googleapis.com/css2?family=Open+Sans:wght@300;400;700&display=swap" rel="stylesheet">
<style>
  :root {
    --stage: #c48a58;
    --card-white: #ffffff;
    --ink-grey: #4d4d4d;
    --ink-black: #1a1a1a;
    --green-light: #c3db5a;
    --green-mid: #7fae3c;
    --green-deep: #3f7f2b;
    --text-on-green: #ffffff;
  }
  * { margin: 0; padding: 0; box-sizing: border-box; }
  html, body {
    width: 1200px;
    height: 407px;
    overflow: hidden;
    background: var(--stage);
    font-family: "Open Sans", Arial, sans-serif;
  }
  .canvas {
    position: relative;
    width: 1200px;
    height: 407px;
  }
  .card {
    position: absolute;
    top: 60px;
    width: 504px;
    height: 288px;
    overflow: hidden;
  }
  .card--front { left: 58px; background: var(--card-white); }
  .card--back {
    left: 638px;
    background: radial-gradient(ellipse 60% 65% at 50% 45%, var(--green-light) 0%, var(--green-mid) 45%, var(--green-deep) 100%);
    display: flex;
    align-items: center;
    justify-content: center;
  }
  .brand {
    display: flex;
    align-items: center;
    gap: 10px;
    font-weight: 300;
    white-space: nowrap;
  }
  .card--front .brand {
    position: absolute;
    top: 68px;
    left: 0;
    right: 0;
    justify-content: center;
    font-size: 30px;
    color: var(--ink-grey);
  }
  .brand__square {
    width: 22px;
    height: 22px;
    background: var(--green-mid);
  }
  .card--back .brand {
    font-size: 38px;
    color: var(--text-on-green);
  }
  .front-sweep {
    position: absolute;
    left: 0;
    top: 0;
    width: 504px;
    height: 288px;
  }
  .contact {
    position: absolute;
    left: 0;
    right: 0;
    color: var(--text-on-green);
    text-align: center;
  }
  .contact__person {
    top: 214px;
    font-size: 14px;
  }
  .contact__name { font-weight: 700; }
  .contact__title { font-weight: 400; font-size: 12.5px; }
  .contact__lines {
    top: 253px;
    font-size: 12px;
    word-spacing: 1px;
  }
  .contact__lines span + span { margin-left: 14px; }
</style>
</head>
<body>
<main class="canvas">
  <section class="card card--front" aria-label="Business card front">
    <svg class="front-sweep" viewBox="0 0 504 288" aria-hidden="true">
      <defs>
        <radialGradient id="sweepGreen" cx="50%" cy="0%" r="75%">
          <stop offset="0%" stop-color="#c3db5a"/>
          <stop offset="45%" stop-color="#7fae3c"/>
          <stop offset="100%" stop-color="#3f7f2b"/>
        </radialGradient>
      </defs>
      <path d="M0,262 Q252,122 504,262 L504,288 L0,288 Z" fill="url(#sweepGreen)"/>
      <path d="M0,248 Q252,104 504,248 Q252,118 0,248 Z" fill="#1a1a1a"/>
    </svg>
    <div class="brand">
      <span class="brand__square"></span>
      <span class="brand__name">Oakridge Developments</span>
    </div>
    <p class="contact contact__person">
      <span class="contact__name">Your Name</span>
      <span class="contact__title">/ Title</span>
    </p>
    <p class="contact contact__lines">
      <span>C : 123-456-7890</span><span>F : 123-456-7890</span><span>E : name@website.com</span>
    </p>
  </section>

  <section class="card card--back" aria-label="Business card back">
    <div class="brand">
      <span class="brand__name">Oakridge Developments</span>
    </div>
  </section>
</main>
</body>
</html>
```